Stylish new business card needed!

Hello everyone! I am in need of a new business card design for an alarm company here in Hurricane WV. I have all fonts, color codes and logos provided for you use! We are a young company and like the style of a clean sleek looking business card. Would like it double sided, one side holding the logo and the other with your design!
Target Market(s)
The people that are looking for the newest tech for home automation and security
Industry/Entity Type
Alarm services; Home automation
Contact Information for Business Card
Name of person; position (Sales; Installer); Phone Number (555.418.7260); Employee cell Number; Website (www.GuardedByVelk.example); Employee Email; Double sided
Look and feel
Each slider illustrates characteristics of the customer's brand and the style your logo design should communicate.

```html
<!DOCTYPE html>
<html lang="en">
<head>
<meta charset="utf-8">
<title>Guarded By Velk – Business Card</title>
<link rel="stylesheet" href="https://fonts.googleapis.com/css2?family=Arimo:wght@400;700&display=swap">
<style>
  :root {
    --orange: #ec8a4c;
    --grey: #979797;
    --ink: #1c1c1c;
    --card-light: #f4f4f4;
    --card-white: #ffffff;
    --backdrop: #e4e5e7;
  }
  * { margin: 0; padding: 0; box-sizing: border-box; }
  html, body {
    width: 1200px; height: 780px; overflow: hidden;
    background: var(--backdrop);
    font-family: "Arimo", Arial, sans-serif;
  }
  .sheet {
    width: 1200px; height: 780px;
    display: flex; align-items: center; justify-content: center; gap: 40px;
  }
  .card {
    position: relative; width: 540px; height: 310px; overflow: hidden;
    box-shadow: 0 6px 18px rgba(0,0,0,.18);
  }
  .card--contact { background: var(--card-light); }
  .card--brand { background: var(--card-white); }

  .swoosh { position: absolute; inset: 0; width: 100%; height: 100%; }

  .wordmark { display: flex; align-items: center; gap: 8px; }
  .wordmark__dot { width: 12px; height: 12px; border-radius: 50%; background: var(--orange); flex: none; }
  .wordmark__name { color: var(--grey); font-weight: 700; letter-spacing: .02em; white-space: nowrap; }
  .tagline { color: var(--orange); font-weight: 700; text-transform: uppercase; letter-spacing: .06em; white-space: nowrap; }

  .card--contact .brand-block { position: absolute; left: 285px; top: 38px; width: 230px; }
  .card--contact .wordmark__name { font-size: 20px; }
  .card--contact .tagline { font-size: 7.5px; margin-top: 6px; margin-left: 20px; }

  .person { position: absolute; left: 70px; top: 62px; }
  .person__name { font-size: 24px; font-weight: 700; line-height: 1; white-space: nowrap; }
  .person__first { color: var(--orange); }
  .person__last { color: var(--grey); }
  .person__role { font-size: 14px; font-weight: 700; color: var(--ink); margin-top: 6px; margin-left: 48px; }

  .divider { position: absolute; left: 255px; top: 130px; width: 2px; height: 92px; background: var(--ink); }

  .contacts { position: absolute; left: 272px; top: 138px; list-style: none; }
  .contacts li { display: flex; align-items: center; gap: 8px; font-size: 15px; color: var(--ink); line-height: 20px; white-space: nowrap; }
  .contacts svg { width: 12px; height: 12px; flex: none; }

  .card--brand .brand-block {
    position: absolute; inset: 0; display: flex; flex-direction: column;
    align-items: center; justify-content: center;
  }
  .card--brand .wordmark { gap: 12px; }
  .card--brand .wordmark__dot { width: 22px; height: 22px; }
  .card--brand .wordmark__name { font-size: 40px; }
  .card--brand .tagline { font-size: 12px; margin-top: 12px; }
</style>
</head>
<body>
<main class="sheet">

  <section class="card card--contact" aria-label="Business card, contact side">
    <svg class="swoosh" viewBox="0 0 540 310" preserveAspectRatio="none" aria-hidden="true">
      <path d="M0,108 C45,232 255,288 485,310 L0,310 Z" fill="var(--orange)"/>
      <path d="M40,82 C70,210 270,276 505,300" fill="none" stroke="var(--grey)" stroke-width="4" stroke-linecap="round"/>
    </svg>

    <div class="brand-block">
      <div class="wordmark">
        <span class="wordmark__dot"></span>
        <span class="wordmark__name">GUARDED BY VELK</span>
      </div>
      <p class="tagline">Automation and Security Services</p>
    </div>

    <div class="person">
      <p class="person__name"><span class="person__first">Mara</span> <span class="person__last">Delvin</span></p>
      <p class="person__role">Sales; Installer</p>
    </div>

    <div class="divider"></div>

    <ul class="contacts">
      <li>
        <svg viewBox="0 0 12 12" aria-hidden="true"><path d="M2.5 1 L4.5 1 L5 3.5 L3.8 4.4 C4.4 5.9 6 7.5 7.6 8.2 L8.5 7 L11 7.5 L11 9.5 C11 10.3 10.3 11 9.5 11 C5 11 1 7 1 2.5 C1 1.7 1.7 1 2.5 1 Z" fill="var(--orange)"/></svg>
        555.418.7260
      </li>
      <li>
        <svg viewBox="0 0 12 12" aria-hidden="true"><rect x="3" y="0.8" width="6" height="10.4" rx="1" fill="none" stroke="var(--orange)" stroke-width="1.2"/><circle cx="6" cy="9.4" r=".6" fill="var(--orange)"/></svg>
        555.290.3814
      </li>
      <li>
        <svg viewBox="0 0 12 12" aria-hidden="true"><circle cx="6" cy="6" r="5" fill="none" stroke="var(--orange)" stroke-width="1.2"/><path d="M1 6 H11 M6 1 C3.5 3.5 3.5 8.5 6 11 M6 1 C8.5 3.5 8.5 8.5 6 11" fill="none" stroke="var(--orange)" stroke-width="1"/></svg>
        www.GuardedByVelk.example
      </li>
      <li>
        <svg viewBox="0 0 12 12" aria-hidden="true"><rect x="0.8" y="2.2" width="10.4" height="7.6" rx="1" fill="none" stroke="var(--orange)" stroke-width="1.2"/><path d="M1 2.6 L6 6.6 L11 2.6" fill="none" stroke="var(--orange)" stroke-width="1.2"/></svg>
        info@GuardedByVelk.example
      </li>
    </ul>
  </section>

  <section class="card card--brand" aria-label="Business card, brand side">
    <div class="brand-block">
      <div class="wordmark">
        <span class="wordmark__dot"></span>
        <span class="wordmark__name">GUARDED BY VELK</span>
      </div>
      <p class="tagline">Automation and Security Services</p>
    </div>
  </section>

</main>
</body>
</html>
```